Impack Proof Screen Protector Packaging Design Project

I want a sleek box design for an Impact Proof Screen Protection Shield" for mobile phones and tablet screens. Want to use this design for online website sale (eCommerce). Please use the colour combination which can effect customers physiology immediately.
Product Features:
Name: vemu Tallguard
Advanced Impact Protection Shield
Easy and Fast Application
Compatible With Stylus
Guaranteed Glue Free
Perfect Crystal Clear
Anti Fingerprint
No Air Bubble
Anti Bacterial
Anti scratch

come on guys...give me some best designs please

Project Deadline Extended
Reason: Have not received the best design yet...

Project Deadline Extended
Reason: still waiting for the best design

Project Deadline Extended

Project Deadline Extended

Project Deadline Extended

Hi,

Thanks for the design. I would like to make some changes.

I want main core colour black (HTML code of Black is 111C24)
Blue colour as aditional or second colour, (HTML code of BLUE is 0088CE)

AND another colour like Orange (HTML -> FF5800)  or Purple (HTML -> 9B1889) can be use as a ACCENT colour if needed.

Pure White, Silver and Greys like -> HTML codes -> 4D4F53 , D1D4D3 , AND C4D9E4 Can be use as support colours if needed.

please work on it and get back to me .

Thanks

Project Deadline Extended
Reason: work pending

UK & Europe is priority and then Global market

Online

• All features must write with Pictures/thumbnail on back side.
Must have a hanger hook / hole.
Must have Recycling sign/logo on the edge.
Must have our website name "vemu.co" on somewhere
its a sleek box design, size - This packing will be in 2 sizes:
a). 27cm X 11cm X 2cm
b). 25cm X 20cm X 2cm
• Impact Protection is main feature in this product, so can be highlighted with some weapon like sword or something like this...
• Please try to not use a picture of any device like lumapad etc. because this packing will be use for number of different king of mobile phone/tablet devices.

```html
<!DOCTYPE html>
<html lang="en">
<head>
<meta charset="utf-8">
<title>vemu Tallguard – Box Front</title>
<link rel="stylesheet" href="https://fonts.googleapis.com/css2?family=Ubuntu:wght@500;700&display=swap">
<style>
  :root {
    --backdrop: #22170f;
    --face-top: #4a7478;
    --face-mid: #25474c;
    --face-bottom: #0f2327;
    --glow: #7fe3ec;
    --band: #3fb8c4;
    --text-white: #ffffff;
    --text-ice: #dff6f8;
    --tagline: #cfe6e9;
    --badge-fill: #2a4e55;
    --badge-edge: #b9dde2;
    --pill-fill: #0e2a2f;
  }
  * { box-sizing: border-box; margin: 0; padding: 0; }
  html, body {
    width: 1132px; height: 1200px; overflow: hidden;
    background: var(--backdrop);
  }
  .canvas {
    position: relative; width: 1132px; height: 1200px;
    font-family: "Ubuntu", "Trebuchet MS", sans-serif;
  }
  .box-front {
    position: absolute; left: 176px; top: 60px;
    width: 780px; height: 1080px;
    overflow: hidden;
    background: linear-gradient(170deg, var(--face-top) 0%, var(--face-mid) 38%, var(--face-bottom) 100%);
    box-shadow: 0 30px 60px rgba(0,0,0,0.55);
  }
  .light-band {
    position: absolute; left: -40px; right: -40px; top: 520px; height: 70px;
    background: radial-gradient(ellipse at 30% 50%, rgba(127,227,236,0.85) 0%, rgba(63,184,196,0.35) 35%, rgba(63,184,196,0) 70%);
    filter: blur(4px);
  }
  .light-band::after {
    content: ""; position: absolute; left: 0; right: 0; top: 32px; height: 4px;
    background: linear-gradient(90deg, rgba(127,227,236,0.2), var(--glow) 30%, rgba(127,227,236,0.1) 90%);
  }
  .feature-list {
    position: absolute; left: 40px; top: 250px;
    list-style: none;
  }
  .feature-list li {
    font-size: 29px; font-weight: 700; line-height: 37px;
    color: var(--text-white);
    text-shadow: 0 0 6px rgba(127,227,236,0.9), 0 0 2px var(--face-bottom);
  }
  .new-badge {
    position: absolute; left: 620px; top: 120px; width: 110px; height: 110px;
  }
  .impact-art {
    position: absolute; left: 480px; top: 240px; width: 110px; height: 160px;
    background: linear-gradient(215deg, rgba(255,255,255,0.9) 0%, rgba(200,240,245,0.35) 35%, rgba(63,184,196,0) 75%);
    clip-path: polygon(85% 0, 100% 12%, 8% 100%, 0 96%);
  }
  .brand-block {
    position: absolute; left: 40px; top: 820px; width: 700px;
  }
  .brand-name {
    display: flex; align-items: flex-end; gap: 22px;
    color: var(--text-ice); font-weight: 700;
  }
  .brand-name .brand-main { font-size: 128px; line-height: 1; letter-spacing: 1px; }
  .brand-side { display: flex; flex-direction: column; padding-bottom: 14px; }
  .brand-tagline {
    font-size: 17px; font-weight: 500; color: var(--tagline); margin-bottom: 2px;
  }
  .brand-sub { font-size: 50px; line-height: 1; }
  .glue-pill {
    position: absolute; left: 440px; top: 150px;
    padding: 6px 16px; border-radius: 18px;
    background: var(--pill-fill); border: 2px solid var(--band);
    color: var(--text-white); font-size: 18px; font-weight: 700;
  }
</style>
</head>
<body>
<main class="canvas">
  <section class="box-front">
    <div class="light-band"></div>

    <ul class="feature-list">
      <li>Easy and Fast Application</li>
      <li>Compatible With Stylus</li>
      <li>Perfect Crystal Clear</li>
      <li>Anti Fingerprint</li>
      <li>No Air Bubble</li>
      <li>Anti Bacterial</li>
      <li>Anti scratch</li>
    </ul>

    <svg class="new-badge" viewBox="0 0 110 110" aria-label="New">
      <polygon fill="var(--badge-fill)" stroke="var(--badge-edge)" stroke-width="3"
        points="55,4 64,20 82,12 83,32 102,35 92,52 104,67 85,74 88,94 69,90 60,106 49,91 31,99 29,79 10,75 19,58 6,43 25,36 24,16 43,21"/>
      <text x="55" y="62" text-anchor="middle" font-family="Ubuntu, sans-serif" font-weight="700" font-size="22" fill="#ffffff">NEW</text>
    </svg>

    <div class="impact-art" role="img" aria-label="Illustration of a projectile striking the screen and leaving a light trail"></div>

    <div class="brand-block">
      <div class="brand-name">
        <span class="brand-main">vemu</span>
        <div class="brand-side">
          <span class="brand-tagline">Advanced Impact Protection Shield</span>
          <span class="brand-sub">Tallguard</span>
        </div>
      </div>
      <span class="glue-pill">Guaranteed Glue Free</span>
    </div>
  </section>
</main>
</body>
</html>
```